My name is Delia Okonkwo,I want to create a web page for my personal dog grooming business. The name on the web page can be "Delia's Dog Grooming" I am located in San Antonio Texas. The page would help grow my customer base. Before and after pictures would display the quality of work that I do. On my page I can provide information about myself, my services, and pricing.
Updates

I have updated project to guaranteed pay

Please try to incorporate a schnauzer in an icon or logo. My dog is a schnauzer. THANKS!!!!!!!!!!!!

Target Market(s)

Dog Owners

Industry/Entity Type

Business

Requirements
Must have
• -A spot for before and after pictures.
-An about me section
-A section to make an appointment
Nice to have
• My favorite Color is purple. I think different shades of purple would be nice or purple with a light green

please incorporate a schnauzer in any icon or logo. My dog is a schnauzer.

```html
<!DOCTYPE html>
<html lang="en">
<head>
<meta charset="utf-8">
<title>Delia's Dog Grooming</title>
<link href="https://fonts.googleapis.com/css2?family=Arimo:wght@400;700&family=Gochi+Hand&family=Kaushan+Script&display=swap" rel="stylesheet">
<style>
:root{
  --plum-deep:#2a0633;
  --plum-dark:#34093f;
  --plum-mid:#4a135c;
  --plum-hero:#5d1a73;
  --plum-hero-light:#8c3aa6;
  --plum-panel:#2d0a3a;
  --plum-box:#9a6ca8;
  --plum-box-top:#6e3a80;
  --lilac-text:#c9a9d3;
  --lilac-head:#c4a9cb;
  --green:#8fd42a;
  --green-dark:#5ea312;
  --white:#ffffff;
  --ink:#1a0420;
}
*{margin:0;padding:0;box-sizing:border-box}
html,body{width:1200px;height:983px;overflow:hidden;background:var(--plum-deep)}
body{font-family:'Arimo',sans-serif;color:var(--lilac-text);position:relative}
.hero{position:absolute;left:0;top:0;width:1200px;height:382px;
  background:radial-gradient(ellipse 300px 260px at 860px 170px,var(--plum-hero-light),transparent 75%),
  linear-gradient(180deg,#4f1563 0%,var(--plum-hero) 60%,#6a1e84 100%)}
.band{position:absolute;left:0;top:382px;width:1200px;height:320px;background:var(--plum-mid)}
.logo{position:absolute;left:127px;top:26px;color:var(--white);font-family:'Gochi Hand',cursive;line-height:1}
.logo .name{font-size:46px;display:block}
.logo .sub{font-size:27px;display:block;margin-left:78px;margin-top:-4px}
.nav{position:absolute;top:0;left:578px;display:flex;gap:9px}
.nav a{display:block;height:63px;width:122px;background:#3a0b4b;color:var(--white);font-weight:700;font-size:15px;text-align:center;line-height:60px;text-decoration:none;position:relative}
.nav a.current::after{content:"";position:absolute;left:12px;right:12px;bottom:0;height:2px;background:var(--green)}
.arrow{position:absolute;border-radius:50%;background:radial-gradient(circle at 40% 35%,#c6f06a,var(--green-dark));display:flex;align-items:center;justify-content:center}
.hero-title{position:absolute;left:131px;top:167px;font-size:31px;line-height:37px;color:var(--lilac-head);font-weight:400}
.hero-text{position:absolute;left:131px;top:294px;width:478px;font-size:12.5px;line-height:15px;color:var(--lilac-text)}
.btn-green{position:absolute;background:linear-gradient(180deg,#c2f05c,var(--green));color:var(--ink);font-weight:700;border-radius:4px;display:flex;align-items:center}
.read-more{left:481px;top:350px;width:128px;height:28px;font-size:13px;padding-left:44px}
.read-more .dot{position:absolute;left:12px;top:6px;width:16px;height:16px;border-radius:50%;background:var(--ink)}
.dogs-photo{position:absolute;left:662px;top:150px;width:372px;height:288px;border-radius:45% 45% 20% 20%;background:radial-gradient(ellipse at 50% 50%,#d7922f,#b5691c 60%,rgba(120,50,110,0) 80%)}
.welcome{position:absolute;left:74px;top:415px;width:1059px;height:260px;background:var(--plum-panel);border-radius:8px}
.welcome h2{position:absolute;left:48px;top:14px;font-family:'Kaushan Script',cursive;font-weight:400;font-size:28px;letter-spacing:2px;color:var(--white)}
.welcome .mark{position:absolute;left:17px;top:25px;width:20px;height:20px;border-radius:50%;background:var(--white)}
.welcome .copy{position:absolute;left:48px;top:60px;width:655px;font-size:12.2px;line-height:15.2px;color:var(--lilac-text);letter-spacing:.55px}
.welcome .copy p+p{margin-top:15px}
.appointment{position:absolute;left:779px;top:48px;width:241px;height:170px;background:var(--plum-box);border-radius:6px;overflow:hidden}
.appointment h3{height:72px;background:var(--plum-box-top);color:var(--white);font-size:18px;font-weight:700;text-align:center;line-height:23px;padding-top:14px}
.appointment .click{left:12px;top:112px;width:150px;height:28px;font-size:15px;padding-left:33px}
.calendar{position:absolute;left:152px;top:82px;width:75px;height:78px;border-radius:4px;background:linear-gradient(180deg,#4aa0d8 0 18%,#f2f2f2 18%)}
.lower{position:absolute;left:0;top:702px;width:1200px;height:238px;background:var(--plum-dark)}
.tab{position:absolute;top:0;height:30px;width:179px;background:#4f1a63;color:var(--lilac-text);font-weight:700;font-size:15px;text-align:center;line-height:30px}
.photo{position:absolute;top:60px;width:131px;height:135px;border:1px solid var(--white)}
.photo.before{left:107px;background:linear-gradient(160deg,#c8c8c8,#f0f0f0 50%,#8a8a8a)}
.photo.after{left:294px;background:linear-gradient(160deg,#e2e2e2,#fafafa 50%,#b0b0b0)}
.contact{position:absolute;left:525px;top:11px;width:609px;height:216px;background:#3b0d4b;border-radius:6px}
.contact label{position:absolute;left:25px;top:24px;font-size:14px;color:var(--lilac-text)}
.contact .msg{position:absolute;left:22px;top:53px;width:314px;height:89px;background:#16021c;border:1px solid #4d1d5e;color:#8a4f9c;font-size:12px;padding:12px}
.send{position:absolute;left:190px;top:162px;width:146px;height:29px;border-radius:6px;background:linear-gradient(180deg,#b5669a,#7a2c63);color:var(--white);font-size:16px;text-align:center;line-height:29px}
.divider{position:absolute;left:367px;top:37px;width:2px;height:146px;background:#6b4878}
.contact h4{position:absolute;left:410px;top:75px;font-family:'Kaushan Script',cursive;font-weight:400;font-size:30px;color:var(--white)}
.social{position:absolute;left:451px;top:178px;display:flex;gap:10px}
.social span{width:28px;height:28px;border-radius:50%;background:#5b4a4f;border:2px solid #2a1a2a;display:flex;align-items:center;justify-content:center}
.stripe{position:absolute;left:0;top:940px;width:1200px;height:7px;background:repeating-linear-gradient(90deg,var(--green) 0 8px,#6dae1c 8px 16px)}
.footer{position:absolute;left:0;top:947px;width:1200px;height:36px;background:#4a1660;text-align:center;font-size:11px;line-height:34px;letter-spacing:.5px;color:var(--lilac-text)}
</style>
</head>
<body>
<div class="hero"></div>
<div class="logo"><span class="name">Delia's</span><span class="sub">Dog Grooming</span></div>

<nav class="nav">
  <a class="current" href="#about">About Me</a>
  <a href="#services">Services</a>
  <a href="#pricing">Pricing</a>
  <a href="#gallery">Photo Gallery</a>
</nav>

<div class="arrow" style="left:51px;top:221px;width:42px;height:42px"><svg width="14" height="16" viewBox="0 0 14 16"><path d="M12 1 L2 8 L12 15Z" fill="#fff"/></svg></div>
<div class="arrow" style="left:1113px;top:221px;width:42px;height:42px"><svg width="14" height="16" viewBox="0 0 14 16"><path d="M2 1 L12 8 L2 15Z" fill="#fff"/></svg></div>

<h1 class="hero-title">NO MESSES IN YOUR CAR,<br>NO SEPARATION<br>ANXIETY</h1>
<p class="hero-text">Our copmany utilize the very latest in mobile grooming technology to ensure your best friends visit with us is a safe and happy times.Our copmany utilize the very latest in mobile grooming technology to ensure your best friends visit with us is a safe and happy times.</p>

<div class="band"></div>
<div class="dogs-photo" role="img" aria-label="Photo of two golden dogs sitting side by side"></div>
<a class="btn-green read-more"><span class="dot"></span>Read more</a>

<section class="welcome" id="about">
  <span class="mark"></span>
  <h2>Welcome</h2>
  <div class="copy">
    <p>Don't forget to check free website templates every day, because we add a new free website template almost daily.You can remove any link to our websites from this template you're free to use the tem-plate without linking back to us. This is just a place holder so you can see how the site would look like.Don't forget to check free website templates every day, because we add a new free website tem-plate almost daily.You can remove any link to our websites from this template you're free to use the template without linking back to us.This is just a place holder so you can see how the site would look like.</p>
    <p>You can remove any link to our websites from this template you're free to use the template without linking back to us.This is just a place holder so you can see how the site would look like.</p>
  </div>
  <div class="appointment">
    <h3>Make an<br>Appointment</h3>
    <a class="btn-green click">Click Here</a>
    <div class="calendar" role="img" aria-label="Illustration of a wall calendar with a clock"></div>
  </div>
</section>

<section class="lower" id="gallery">
  <div class="tab" style="left:74px">Before Grooming</div>
  <div class="tab" style="left:270px">After Grooming</div>
  <div class="arrow" style="left:60px;top:115px;width:24px;height:24px"><svg width="8" height="10" viewBox="0 0 8 10"><path d="M7 0 L0 5 L7 10Z" fill="#fff"/></svg></div>
  <div class="photo before" role="img" aria-label="Photo of a white terrier before grooming"></div>
  <div class="photo after" role="img" aria-label="Photo of a white terrier after grooming"></div>
  <div class="arrow" style="left:444px;top:112px;width:24px;height:24px"><svg width="8" height="10" viewBox="0 0 8 10"><path d="M1 0 L8 5 L1 10Z" fill="#fff"/></svg></div>

  <div class="contact">
    <label>I'd also like to leave a message for you:</label>
    <div class="msg">Your message</div>
    <div class="send">Send enquiry</div>
    <div class="divider"></div>
    <h4>Conatct Us</h4>
    <div class="social">
      <span></span>
      <span><svg width="14" height="10" viewBox="0 0 14 10"><rect x=".5" y=".5" width="13" height="9" fill="#eee"/><path d="M.5 .5 L7 6 L13.5 .5" fill="none" stroke="#5b4a4f"/></svg></span>
      <span></span>
      <span></span>
    </div>
  </div>
</section>

<div class="stripe"></div>
<footer class="footer">COPYRIGHT © 2011 DELIASGROOMING.COM. ALL RIGHTS RESERVED</footer>
</body>
</html>
```